Web Design for Webdesign company 3 page PSD

Project
---------
We need a PSD Web Design to be used in a WordPress installation.
What we would like to create is a professional looking website for a web design agency. We also need you to look for suitable stock images to be placed on these pages.
We need the design for:
Homepage
Landing page
Contact page
attached in the pages file you will find a file with more in depth details how these files should be build up.
We would like to see a desktop version and a mobile version of these pages
The website should have a 1100px width.
The mobile design should have 480px width.
The homepage should have a header slider about 450px high.
The slider is preferred full width and should have some images text and a button
Objectives
-------------
The main objective for the website is to get leads from customers in the form of a request for a quotation or a call or mail me back action. The most important action for the homepage is to link and navigate to our landing pages.
What we want to tell our visitors (our main products)
-------------------------------------------------------------------
- A website with no big investment but a monthly rate
- A successful website with no worries (a complete website, seo, hosting and a service contract for future customization is included for a monthly rate)
Color Scheme
------------
Use branding colors. You can find them in the branding.pdf file.
Additional colors:
White: #ffffff
Black: #181818
Company info
--------------
We are a starting web design / marketing agency based in The Netherlands and looking for the design of our website. Our services are (custom) webdesign, website marketing or combinations of both. Our main customer group is small business owners.
We sell websites but give the option to buy it with a lease contract.
A second product is a default website with a complete service: SEO, hosting and a service contract for a monthly rate.
Content:
-----------
If not available place Lorem Ipsum text.
There will come about 400 words of text on the landing pages
Design Competition
--------------------------
Since this is a designing competition we would like to see your creativity.
What you can expect from us is a lot of feedback 7 days a week with short response time.
You can send us the first sketchy mock ups of the homepage and we will give feedback based on these design. But we like your feedback or comments as well
Read the pages file for more in depth details how the pages should be designed

Target Market(s)
Small business owners in The Netherlands
Industry/Entity Type
It Company
Number of Pages Required
3 page
Requirements
Must have
- Homepage:
- Header slider with images, some text and a link to a custom page
- The slider should have 3 designed slides
- Landings page:
- Sidebar
- Action button for a request for a quotation
- Action button for a call me back action
- Action button for an appointment
- Contact form:
- Address details
- Contact form
Nice to have
- Homepage:
- Full width slider
- Testimonial block
- Blog items
Should not have
- Flash
- A to crowded design

```html
<!DOCTYPE html>
<html lang="en">
<head>
<meta charset="utf-8">
<title>Brightmill Web Studio – Landing</title>
<link rel="stylesheet" href="https://fonts.googleapis.com/css2?family=Arimo:wght@400;700&family=Open+Sans:wght@400;600&display=swap">
<style>
:root{
  --teal:#2e6e80;
  --green:#5b9378;
  --orange:#f7990c;
  --ink:#181818;
  --text:#555;
  --line:#e6e6e6;
  --side-bg:#ececec;
  --footer:#323232;
  --footer-bottom:#262626;
  --white:#ffffff;
}
*{box-sizing:border-box;margin:0;padding:0}
html,body{width:1200px;height:2338px;overflow:hidden}
body{position:relative;background:var(--white);font-family:"Open Sans",Arial,sans-serif;color:var(--text)}
.abs{position:absolute}

/* header */
.site-header{position:absolute;left:0;top:0;width:1200px;height:109px}
.brand{left:94px;top:28px;display:flex;align-items:center;gap:12px}
.brand-mark{width:44px;height:44px;border-radius:50%;background:var(--green)}
.brand-name{font-family:Arimo,Arial,sans-serif;font-weight:700;color:var(--teal);font-size:21px;line-height:44px}
.main-nav{right:93px;top:40px;display:flex;gap:26px;align-items:center}
.main-nav a{font-family:Arimo,Arial,sans-serif;font-weight:700;font-size:15px;color:#444;text-decoration:none;padding:6px 0}
.main-nav a.active{background:#555;color:var(--white);border-radius:16px;padding:6px 20px}

.page-banner{left:0;top:109px;width:1200px;height:91px;background:linear-gradient(90deg,#4f8f68,#72a885 30%,#5f9874 55%,#3f7d59 75%,#6aa17e)}
.page-banner h1{position:absolute;left:92px;top:32px;font-family:Arimo,Arial,sans-serif;font-size:24px;color:var(--white)}

/* sidebar */
.quick-links{left:92px;top:228px;width:224px;list-style:none}
.quick-links li{height:38px;background:var(--side-bg);border-bottom:2px solid var(--white);font-size:15px;color:#999;padding:0 16px;display:flex;align-items:center;justify-content:space-between}
.quick-links li::after{content:"›";font-size:20px;color:#aaa}
.quick-links li.active{background:var(--teal);color:var(--white)}
.quick-links li.active::after{color:var(--white)}

/* intro */
.intro{left:345px;top:224px;width:335px}
.intro h2{font-family:Arimo,Arial,sans-serif;font-weight:700;color:var(--ink);font-size:26px;line-height:26px}
.intro h2 span{display:block;color:var(--teal);font-size:42px;line-height:44px;white-space:nowrap}
.body-copy{font-size:12.5px;line-height:18.5px;color:#555;margin-top:12px}
.devices{left:700px;top:330px;width:408px;height:222px;border-radius:6px;background:linear-gradient(135deg,#5a6b7d 0%,#8fb7d4 45%,#f0c96a 70%,#f26b6b 100%);opacity:.85}

.divider{left:345px;width:762px;height:1px;background:var(--line)}

/* services */
.service{left:345px;width:762px;height:260px}
.service-icon{position:absolute;left:0;top:30px;width:150px;height:140px;border-radius:16px}
.icon-green{background:var(--green)}
.icon-orange{background:var(--orange)}
.icon-teal{background:var(--teal)}
.service-text{position:absolute;left:179px;top:26px;width:340px}
.service-text h3{font-family:Arimo,Arial,sans-serif;font-weight:700;font-size:22px;line-height:26px;color:var(--ink)}
.service-text h3 span{color:var(--teal)}
.service-text.orange h3 span{color:var(--orange)}
.service-text.green h3 span{color:var(--green)}
.service-text .body-copy{margin-top:8px}
.service-list{position:absolute;left:545px;top:0;width:217px;height:250px;border-left:3px solid #eee;border-radius:34px 0 0 34px;list-style:none;padding:50px 0 0 28px}
.service-list li{font-size:12.5px;color:#555;height:32px;display:flex;align-items:center;gap:9px}
.service-list svg{flex:none}

/* actions */
.cta{top:1706px;width:230px;height:203px;display:flex;flex-direction:column;align-items:center;justify-content:flex-end;padding-bottom:22px;color:var(--white);font-family:Arimo,Arial,sans-serif;font-weight:700;font-size:18px;line-height:20px;text-align:center;text-decoration:none}
.cta-figure{width:90px;height:90px;border-radius:12px;background:rgba(255,255,255,.3);margin-bottom:20px}
.cta-call{left:345px;background:var(--green)}
.cta-appointment{left:612px;background:var(--orange)}
.cta-quote{left:877px;background:var(--teal)}

/* footer */
.site-footer{left:0;top:1966px;width:1200px;height:300px;background:var(--footer)}
.footer-col{position:absolute;top:53px}
.footer-col h4{font-family:Arimo,Arial,sans-serif;font-weight:700;color:var(--white);font-size:15px;line-height:18px;margin-bottom:18px}
.footer-col a,.footer-col p{display:block;color:#bbb;font-size:13px;line-height:24px;text-decoration:none}
.newsletter{left:92px}
.newsletter h4{font-size:17px;line-height:20px}
.field{width:243px;height:32px;background:var(--white);border-radius:3px;margin-bottom:10px;font-size:12px;color:#999;padding:0 12px;display:flex;align-items:center}
.subscribe{width:243px;height:33px;background:var(--green);border-radius:3px;color:var(--white);font-family:Arimo,Arial,sans-serif;font-weight:700;font-size:14px;display:flex;align-items:center;justify-content:center}
.contact-item{display:flex;gap:12px;margin-bottom:12px}
.contact-item svg{flex:none;margin-top:3px}
.contact-item p{line-height:19px}
.social-item{display:flex;align-items:center;gap:12px;margin-bottom:18px;color:#bbb;font-size:13px}
.social-dot{width:28px;height:28px;border-radius:50%;border:2px solid #888;flex:none}
.footer-bottom{left:0;top:2266px;width:1200px;height:72px;background:var(--footer-bottom);color:#bbb;font-size:13px;text-align:center;padding-top:15px;line-height:22px}
</style>
</head>
<body>

<header class="site-header">
  <div class="abs brand">
    <span class="brand-mark"></span>
    <span class="brand-name">BRIGHTMILL WEB STUDIO</span>
  </div>
  <nav class="abs main-nav">
    <a href="#">HOME</a>
    <a href="#" class="active">LANDING</a>
    <a href="#">TESTIMONIALS</a>
    <a href="#">BLOG</a>
    <a href="#">CONTACT</a>
  </nav>
</header>

<section class="abs page-banner"><h1>LANDING</h1></section>

<ul class="abs quick-links">
  <li>Quick Link 01</li><li class="active">Quick Link 02</li><li>Quick Link 03</li><li>Quick Link 04</li><li>Quick Link 05</li>
  <li>Quick Link 06</li><li>Quick Link 07</li><li>Quick Link 08</li><li>Quick Link 09</li><li>Quick Link 10</li>
</ul>

<section class="abs intro">
  <h2>WE BUILD FULL<span>SERVICE WEBSITE</span></h2>
  <p class="body-copy">Lorem ipsum dolor sit amet, cu per augue graeco cotidieque. Est ut novum laudem definiebas, no augue necessitatibus nam. Te erant dissentias appellantur cum, errem mentitum conceptam ad eum. Ad has meis adipisci, eu sed iracundia reprimique, eius perpetua vis te. Fuisset democritum scribentur ex est, mei ei viderer sapientem suscipiantur.</p>
  <p class="body-copy" style="margin-top:18px">Euismod appareat explicari et quo. Mei in natum errem scribentur, idque affert abhorreant et pri, ex eum torquatos adolescens. Erroribus conclusionemque cu quo. Novum putent his eu.</p>
</section>
<div class="abs devices" role="img" aria-label="Illustration of a desktop monitor, laptop, tablet and phone showing a website"></div>

<div class="abs divider" style="top:612px"></div>

<section class="abs service" style="top:662px">
  <div class="service-icon icon-green" role="img" aria-label="Browser window icon with a check mark"></div>
  <div class="service-text green">
    <h3>A SUCCESSFUL <span>WEBSITE</span></h3>
    <p class="body-copy">Lorem ipsum dolor sit amet, cu per augue graeco cotidieque. Est ut novum laudem definiebas, no augue necessitatibus nam. Te erant dissentias appellantur cum, errem mentitum conceptam ad eum. Ad has meis adipisci, eu sed iracundia reprimique, eius perpetua vis te. Fuisset democritum scribentur ex est, mei ei viderer sapientem suscipiantur.</p>
  </div>
  <ul class="service-list">
    <li><svg width="14" height="14" viewBox="0 0 14 14"><rect x=".5" y=".5" width="13" height="13" fill="none" stroke="var(--green)"/><path d="M3 7l3 3 5-6" stroke="var(--green)" stroke-width="2" fill="none"/></svg>Lorem Ipsum Service 01</li>
    <li><svg width="14" height="14" viewBox="0 0 14 14"><rect x=".5" y=".5" width="13" height="13" fill="none" stroke="var(--green)"/><path d="M3 7l3 3 5-6" stroke="var(--green)" stroke-width="2" fill="none"/></svg>Lorem Ipsum Service 02</li>
    <li><svg width="14" height="14" viewBox="0 0 14 14"><rect x=".5" y=".5" width="13" height="13" fill="none" stroke="var(--green)"/><path d="M3 7l3 3 5-6" stroke="var(--green)" stroke-width="2" fill="none"/></svg>Lorem Ipsum Service 03</li>
    <li><svg width="14" height="14" viewBox="0 0 14 14"><rect x=".5" y=".5" width="13" height="13" fill="none" stroke="var(--green)"/><path d="M3 7l3 3 5-6" stroke="var(--green)" stroke-width="2" fill="none"/></svg>Lorem Ipsum Service 04</li>
    <li><svg width="14" height="14" viewBox="0 0 14 14"><rect x=".5" y=".5" width="13" height="13" fill="none" stroke="var(--green)"/><path d="M3 7l3 3 5-6" stroke="var(--green)" stroke-width="2" fill="none"/></svg>Lorem Ipsum Service 05</li>
  </ul>
</section>

<div class="abs divider" style="top:964px"></div>

<section class="abs service" style="top:1013px">
  <div class="service-icon icon-orange" role="img" aria-label="Globe icon with a pointer cursor"></div>
  <div class="service-text orange">
    <h3>SEO OPTIMIZED WITH A<br><span>SERVICE CONTRACT</span></h3>
    <p class="body-copy">Lorem ipsum dolor sit amet, cu per augue graeco cotidieque. Est ut novum laudem definiebas, no augue necessitatibus nam. Te erant dissentias appellantur cum, errem mentitum conceptam ad eum. Ad has meis adipisci, eu sed iracundia reprimique, eius perpetua vis te. Fuisset democritum scribentur ex est, mei ei viderer sapientem suscipiantur.</p>
  </div>
  <ul class="service-list">
    <li><svg width="14" height="14" viewBox="0 0 14 14"><rect x=".5" y=".5" width="13" height="13" fill="none" stroke="var(--orange)"/><path d="M3 7l3 3 5-6" stroke="var(--orange)" stroke-width="2" fill="none"/></svg>Lorem Ipsum Service 01</li>
    <li><svg width="14" height="14" viewBox="0 0 14 14"><rect x=".5" y=".5" width="13" height="13" fill="none" stroke="var(--orange)"/><path d="M3 7l3 3 5-6" stroke="var(--orange)" stroke-width="2" fill="none"/></svg>Lorem Ipsum Service 02</li>
    <li><svg width="14" height="14" viewBox="0 0 14 14"><rect x=".5" y=".5" width="13" height="13" fill="none" stroke="var(--orange)"/><path d="M3 7l3 3 5-6" stroke="var(--orange)" stroke-width="2" fill="none"/></svg>Lorem Ipsum Service 03</li>
    <li><svg width="14" height="14" viewBox="0 0 14 14"><rect x=".5" y=".5" width="13" height="13" fill="none" stroke="var(--orange)"/><path d="M3 7l3 3 5-6" stroke="var(--orange)" stroke-width="2" fill="none"/></svg>Lorem Ipsum Service 04</li>
    <li><svg width="14" height="14" viewBox="0 0 14 14"><rect x=".5" y=".5" width="13" height="13" fill="none" stroke="var(--orange)"/><path d="M3 7l3 3 5-6" stroke="var(--orange)" stroke-width="2" fill="none"/></svg>Lorem Ipsum Service 05</li>
  </ul>
</section>

<div class="abs divider" style="top:1319px"></div>

<section class="abs service" style="top:1364px">
  <div class="service-icon icon-teal" role="img" aria-label="Cloud and server stack hosting icon"></div>
  <div class="service-text">
    <h3>HOSTING <span>SERVICE</span></h3>
    <p class="body-copy">Lorem ipsum dolor sit amet, cu per augue graeco cotidieque. Est ut novum laudem definiebas, no augue necessitatibus nam. Te erant dissentias appellantur cum, errem mentitum conceptam ad eum. Ad has meis adipisci, eu sed iracundia reprimique, eius perpetua vis te. Fuisset democritum scribentur ex est, mei ei viderer sapientem suscipiantur.</p>
  </div>
  <ul class="service-list">
    <li><svg width="14" height="14" viewBox="0 0 14 14"><rect x=".5" y=".5" width="13" height="13" fill="none" stroke="var(--teal)"/><path d="M3 7l3 3 5-6" stroke="var(--teal)" stroke-width="2" fill="none"/></svg>Lorem Ipsum Service 01</li>
    <li><svg width="14" height="14" viewBox="0 0 14 14"><rect x=".5" y=".5" width="13" height="13" fill="none" stroke="var(--teal)"/><path d="M3 7l3 3 5-6" stroke="var(--teal)" stroke-width="2" fill="none"/></svg>Lorem Ipsum Service 02</li>
    <li><svg width="14" height="14" viewBox="0 0 14 14"><rect x=".5" y=".5" width="13" height="13" fill="none" stroke="var(--teal)"/><path d="M3 7l3 3 5-6" stroke="var(--teal)" stroke-width="2" fill="none"/></svg>Lorem Ipsum Service 03</li>
    <li><svg width="14" height="14" viewBox="0 0 14 14"><rect x=".5" y=".5" width="13" height="13" fill="none" stroke="var(--teal)"/><path d="M3 7l3 3 5-6" stroke="var(--teal)" stroke-width="2" fill="none"/></svg>Lorem Ipsum Service 04</li>
    <li><svg width="14" height="14" viewBox="0 0 14 14"><rect x=".5" y=".5" width="13" height="13" fill="none" stroke="var(--teal)"/><path d="M3 7l3 3 5-6" stroke="var(--teal)" stroke-width="2" fill="none"/></svg>Lorem Ipsum Service 05</li>
  </ul>
</section>

<div class="abs divider" style="top:1669px"></div>

<a class="abs cta cta-call" href="#">
  <div class="cta-figure" role="img" aria-label="Support agent with headset icon"></div>
  CALL ME BACK
</a>
<a class="abs cta cta-appointment" href="#">
  <div class="cta-figure" role="img" aria-label="Calendar icon with a pen"></div>
  MAKE AN<br>APPOINTMENT
</a>
<a class="abs cta cta-quote" href="#">
  <div class="cta-figure" role="img" aria-label="Document icon with a pen"></div>
  REQUEST<br>A QUOTATION
</a>

<footer class="abs site-footer">
  <div class="footer-col newsletter">
    <h4>SUBSCRIBE TO<br>OUR NEWSLETTER</h4>
    <div class="field">Enter Your Name</div>
    <div class="field">Enter Your Email</div>
    <div class="subscribe">SUBSCRIBE</div>
  </div>
  <div class="footer-col" style="left:405px">
    <h4>QUICK LINKS</h4>
    <a href="#">Home</a><a href="#">Landing</a><a href="#">Testimonials</a><a href="#">Blog</a><a href="#">Contact</a>
  </div>
  <div class="footer-col" style="left:612px">
    <h4>CONTACT INFO</h4>
    <div class="contact-item">
      <svg width="12" height="16" viewBox="0 0 12 16"><path d="M6 0a6 6 0 0 0-6 6c0 4 6 10 6 10s6-6 6-10a6 6 0 0 0-6-6z" fill="#999"/><circle cx="6" cy="6" r="2" fill="#323232"/></svg>
      <p>228, lorem ipsum dolor sit,<br>dosis miunf- 845848</p>
    </div>
    <div class="contact-item">
      <svg width="14" height="14" viewBox="0 0 14 14"><path d="M3 0l3 3-2 2a8 8 0 0 0 5 5l2-2 3 3-2 3C5 14 0 9 0 3z" fill="#999"/></svg>
      <p>Phone: (555)010-42-7731<br>Fax: (555)010-42-7790</p>
    </div>
    <div class="contact-item">
      <svg width="14" height="12" viewBox="0 0 14 12"><rect y="2" width="14" height="10" fill="#999"/><path d="M0 2l7 5 7-5" stroke="#323232" fill="none"/></svg>
      <p>Email: info@brightmill.example<br>Website:www.brightmill.example</p>
    </div>
  </div>
  <div class="footer-col" style="left:882px">
    <h4>STAY CONNECTED</h4>
    <div class="social-item"><span class="social-dot"></span>Follow Us On Friendsboard</div>
    <div class="social-item"><span class="social-dot"></span>Follow Us On Chirper</div>
    <div class="social-item"><span class="social-dot"></span>Follow Us On WorkLink</div>
  </div>
</footer>
<div class="abs footer-bottom">© 2015 Brightmill All Rights Reserved.<br>Terms of Use | Legal Disclaimer | Privacy Policy | References</div>

</body>
</html>
```